Manuka Honey company needs a Upmarket, Luxury Website!

New Zealand, Taranaki based Manuka Honey company Rimu Vale Honey is looking for a new website, we are looking for an upmarket, luxury, serious website design. We export the highest quality quality Manuka Honey, straight from the Taranaki region.

Main export markets are Asia & Europe, also New Zealand & Australia.

Looking to have a beautiful, upmarket, serious, luxurious & graphical experience with mobile optimization in mind. Like the use of product staging/mockups

You can use copy from other websites to build the site and we will change the copy after the design is finished.

***Please include 'Honey Product' mockups in website.

*Will add illustrator files in coming days***

Feel free to make website functional in Shopify, Wordpress or WIX

Target Market(s)

Asia, Europe (main markets) New Zealand, Australia (Submarkets)

Coding

Coded - Design and coding required

Number of Pages Required

4 page

Requirements
Must have
• Home, Shop, About Us, Contact Us

Homepage to include:

Our Products
Company Video (video under construction)
What is MGO/KPS
Newsletter Opt-in

***(Not in Order)***

Please include 'Honey Product' mockups in website.
*Will add illustrator files in coming days
Nice to have
• FAQ & Partnership Inquiries (hyperlink in footer)

```html
<!DOCTYPE html>
<html lang="en">
<head>
<meta charset="utf-8">
<title>Rimu Vale Honey</title>
<link href="https://fonts.googleapis.com/css2?family=Jost:wght@400;500;600;700&family=Lato:wght@400;700&display=swap" rel="stylesheet">
<style>
:root{
  --ink:#1f1f1f;
  --muted:#555;
  --gold-a:#c6a451;
  --gold-b:#f1e3a0;
  --cream:#f6efd9;
  --sand:#e9dcb3;
  --footer:#111;
  --white:#fff;
}
*{margin:0;padding:0;box-sizing:border-box}
html,body{width:1200px;height:3838px;overflow:hidden}
body{position:relative;background:var(--white);font-family:'Lato',sans-serif;color:var(--ink)}
.abs{position:absolute}
.heading{font-family:'Jost',sans-serif;font-weight:600;letter-spacing:4px;color:var(--ink)}
.gold-rule{position:absolute;height:4px;width:75px;background:linear-gradient(90deg,var(--gold-a),var(--gold-b))}
.btn{position:absolute;display:flex;align-items:center;justify-content:center;border-radius:30px;
  background:linear-gradient(90deg,var(--gold-a),var(--gold-b));font-family:'Jost',sans-serif;font-weight:600;
  font-size:12px;letter-spacing:2px;color:#3a2f12;box-shadow:0 0 0 3px #fff,0 0 0 4px var(--gold-a)}
.jar{position:absolute;border-radius:14px 14px 22px 22px;box-shadow:0 14px 22px rgba(0,0,0,.3)}
.jar::before{content:"";position:absolute;left:0;right:0;top:0;height:24%;background:#1c1c1c;border-radius:14px 14px 0 0}

/* header + hero */
.hero{position:absolute;left:0;top:0;width:1200px;height:730px;
  background:linear-gradient(180deg,#eae2bf 0%,#e3d8ad 45%,#efe7c9 75%,#fbf8ee 100%)}
.logo{position:absolute;left:90px;top:22px;display:flex;align-items:center;gap:14px}
.logo-dot{width:44px;height:44px;border-radius:50%;background:#3c3c3c}
.logo-name{font-family:'Jost',sans-serif;font-size:26px;letter-spacing:3px;color:#3c3c3c;font-weight:400}
.nav{position:absolute;top:38px;font-family:'Jost',sans-serif;font-size:13px;color:var(--ink);letter-spacing:.5px}
.nav.active{font-weight:600}
.hero-title{position:absolute;left:0;width:1200px;top:136px;text-align:center;font-size:57px;letter-spacing:6px;font-weight:700}
.hero-sub{position:absolute;left:0;width:1200px;top:207px;text-align:center;font-family:'Jost',sans-serif;font-size:30px;letter-spacing:4px;color:var(--ink)}
.arrow{position:absolute;top:325px}

/* mgo */
.mgo-blob{position:absolute;left:82px;top:760px;width:492px;height:477px;border-radius:58% 42% 50% 50%/55% 45% 55% 45%;
  background:linear-gradient(135deg,#e8d69a,#caa95b)}
.mgo-photo{position:absolute;left:108px;top:776px;width:440px;height:440px;border-radius:50%;
  background:radial-gradient(circle at 40% 40%,#d9a53a 0%,#9a6f2c 30%,#d8d0c0 55%,#f3f1ec 80%)}
.body-text{font-size:13px;line-height:21.8px;color:var(--muted)}

/* products */
.products{position:absolute;left:0;top:1342px;width:1200px;height:663px;
  background:radial-gradient(ellipse at 70% 30%,#f6ecc6 0%,#fbf6e6 40%,#f7efd6 70%,#fdfbf3 100%)}
.product{position:absolute;width:260px;text-align:center}
.product-name{font-family:'Jost',sans-serif;font-size:18px;font-weight:500;margin-top:0}
.product-desc{font-size:11px;line-height:18px;color:var(--muted);margin-top:6px}
.dot{position:absolute;top:1942px;width:12px;height:12px;border-radius:50%;border:1px solid #ddd;background:#fff}
.dot.on{background:#111;border-color:#111}

/* video */
.video{position:absolute;left:259px;top:2231px;width:710px;height:407px;
  background:linear-gradient(160deg,#8d8d8d 0%,#6f6f6f 40%,#7c6650 70%,#6a6a6a 100%);box-shadow:0 12px 30px rgba(0,0,0,.2)}
.play{position:absolute;left:0;bottom:0;width:91px;height:67px;background:linear-gradient(90deg,var(--gold-a),var(--gold-b));
  display:flex;align-items:center;justify-content:center}

/* faq */
.faq{position:absolute;left:0;top:2758px;width:1200px;height:678px;background:linear-gradient(135deg,#f4ecd3,#e9dcb3)}
.faq-item{position:absolute;left:107px;width:492px;border:1px solid #9a9a9a;font-family:'Jost',sans-serif;font-size:13px;font-weight:500;padding:0 26px;color:var(--ink)}
.faq-item .q{height:48px;display:flex;align-items:center;justify-content:space-between}
.faq-item .a{font-family:'Lato',sans-serif;font-weight:400;font-size:11.5px;line-height:17.5px;color:#444;padding-right:10px}
.faq-ring{position:absolute;left:663px;top:2870px;width:458px;height:454px;border-radius:50%;background:#d8c898}
.faq-photo{position:absolute;left:690px;top:2882px;width:430px;height:430px;border-radius:50%;
  background:radial-gradient(circle at 55% 45%,#f7f3e6 0%,#f0c870 35%,#d99a2a 60%,#c99b4b 80%)}

/* footer */
.footer{position:absolute;left:0;top:3436px;width:1200px;height:402px;background:var(--footer);color:#ddd}
.f-head{position:absolute;top:79px;font-family:'Jost',sans-serif;font-weight:600;font-size:15px;letter-spacing:2.5px;color:#fff}
.f-links{position:absolute;top:115px;font-size:13px;line-height:29.8px;color:#ddd;list-style:none}
.f-social li{display:flex;align-items:center;gap:14px}
.f-social i{display:inline-block;width:12px;height:12px;border-radius:50%;background:#fff}
.email{position:absolute;left:605px;top:145px;width:233px;height:34px;background:#fff;font-size:10px;color:#555;display:flex;align-items:center;padding-left:18px;letter-spacing:.5px}
.subscribe{position:absolute;left:605px;top:191px;width:233px;height:36px;background:linear-gradient(90deg,var(--gold-a),var(--gold-b));
  font-family:'Jost',sans-serif;font-weight:600;font-size:13px;color:#222;display:flex;align-items:center;justify-content:center;letter-spacing:.5px}
.copy{position:absolute;left:0;width:1200px;top:362px;text-align:center;font-size:12px;color:#bbb}
</style>
</head>
<body>

<section class="hero">
  <div class="abs" role="img" aria-label="Soft misty landscape with a snow-capped mountain over a lake" style="left:0;top:160px;width:1200px;height:420px;background:radial-gradient(ellipse at 50% 40%,#d7cb9b 0%,rgba(227,216,173,0) 65%)"></div>
  <div class="logo"><span class="logo-dot"></span><span class="logo-name">RIMU VALE HONEY</span></div>
  <a class="nav active" style="left:587px">HOME</a>
  <a class="nav" style="left:702px">SHOP</a>
  <a class="nav" style="left:817px">ABOUT US</a>
  <a class="nav" style="left:961px">CONTACT US</a>
  <h1 class="heading hero-title">BEST MANUKA HONEY</h1>
  <p class="hero-sub">HONEY YOUR WILL NEVER TASTE!</p>
  <svg class="arrow" style="left:74px" width="26" height="50" viewBox="0 0 26 50"><path d="M24 2 L3 25 L24 48" fill="none" stroke="#999" stroke-width="3"/></svg>
  <svg class="arrow" style="left:1100px" width="26" height="50" viewBox="0 0 26 50"><path d="M2 2 L23 25 L2 48" fill="none" stroke="#999" stroke-width="3"/></svg>
  <div class="jar" role="img" aria-label="Green manuka honey jar" style="left:240px;top:358px;width:225px;height:280px;background:linear-gradient(90deg,#0f4a2c,#1f7a46 60%,#0f4a2c)"></div>
  <div class="jar" role="img" aria-label="Purple manuka honey jar" style="left:735px;top:335px;width:215px;height:300px;background:linear-gradient(90deg,#3c1a63,#6b2fa3 60%,#3c1a63)"></div>
  <div class="jar" role="img" aria-label="Large orange premium manuka honey jar" style="left:440px;top:295px;width:305px;height:345px;background:linear-gradient(90deg,#7a2a10,#c24a1c 55%,#6b220c)"></div>
</section>

<section>
  <div class="mgo-blob"></div>
  <div class="mgo-photo" role="img" aria-label="Close-up of a bee gathering nectar on a white manuka flower"></div>
  <div class="jar" role="img" aria-label="Black manuka honey jar" style="left:374px;top:1045px;width:198px;height:226px;background:linear-gradient(90deg,#111,#2b2b2b 60%,#111)"></div>
  <h2 class="heading abs" style="left:620px;top:822px;font-size:34px">WHAT IS MGO</h2>
  <div class="gold-rule" style="left:623px;top:876px"></div>
  <div class="abs body-text" style="left:623px;top:898px;width:470px">
    <p>Lorem Ipsum is simply dummy text of the printing and typesetting industry. Lorem Ipsum has been the industry's standard dummy text ever since the 1500s, when an unknown printer took a galley of type and scrambled it to make a type specimen book. It has survived not only five centuries</p>
    <p style="margin-top:22px">was popularised in the 1960s with the release of Letterfold sheets containing Lorem Ipsum passages, and more recently with desktop publishing software like Quillset Layout including versions of Lorem Ipsum</p>
  </div>
  <a class="btn" style="left:626px;top:1112px;width:180px;height:46px">LEARN MORE</a>
</section>

<section class="products">
  <h2 class="heading abs" style="left:0;width:1200px;text-align:center;top:42px;font-size:33px">OUR PRODUCTS</h2>
  <div class="gold-rule" style="left:556px;top:96px"></div>
</section>
<div class="jar" role="img" aria-label="Red manuka honey jar" style="left:168px;top:1492px;width:186px;height:214px;background:linear-gradient(90deg,#6d0f1d,#b3193a 60%,#6d0f1d)"></div>
<div class="jar" role="img" aria-label="Purple manuka honey jar" style="left:498px;top:1492px;width:186px;height:214px;background:linear-gradient(90deg,#3c1a63,#6b2fa3 60%,#3c1a63)"></div>
<div class="jar" role="img" aria-label="Matte black manuka honey jar" style="left:850px;top:1492px;width:158px;height:204px;background:linear-gradient(90deg,#111,#2a2a2a 60%,#111)"></div>
<div class="product" style="left:131px;top:1728px"><p class="product-name">Mounka Honey</p><p class="product-desc">Lorem Ipsum is simply dummy text of the<br>printing ly dummy text</p></div>
<div class="product" style="left:459px;top:1728px"><p class="product-name">Mounka Honey</p><p class="product-desc">Lorem Ipsum is simply dummy text of the<br>printing ly dummy text</p></div>
<div class="product" style="left:797px;top:1728px"><p class="product-name">Mounka Honey</p><p class="product-desc">Lorem Ipsum is simply dummy text of the<br>printing ly dummy text</p></div>
<a class="btn" style="left:184px;top:1817px;width:154px;height:40px;font-size:11px">LEARN MORE</a>
<a class="btn" style="left:514px;top:1817px;width:154px;height:40px;font-size:11px">LEARN MORE</a>
<a class="btn" style="left:853px;top:1817px;width:154px;height:40px;font-size:11px">LEARN MORE</a>
<span class="dot on" style="left:567px"></span>
<span class="dot" style="left:589px"></span>
<span class="dot" style="left:611px"></span>

<section>
  <h2 class="heading abs" style="left:0;width:1200px;text-align:center;top:2059px;font-size:35px">OUR COMPANY VIDEO</h2>
  <div class="gold-rule" style="left:562px;top:2110px"></div>
  <p class="abs" style="left:0;width:1200px;text-align:center;top:2139px;font-size:15px;line-height:21px;color:#555">Lorem Ipsum is simply dummy text of the printing and typesetting industry. Lorem<br>Ipsum has been the industry's standard dummy.</p>
  <div class="video" role="img" aria-label="Still of a honey dipper resting in a bowl of honey beside pink flowers">
    <p class="heading abs" style="left:0;width:710px;text-align:center;top:188px;font-size:24px;color:#fff">PLAY VIDEO</p>
    <div class="play"><svg width="24" height="30" viewBox="0 0 24 30"><path d="M2 1 L23 15 L2 29 Z" fill="#111"/></svg></div>
  </div>
</section>

<section class="faq">
  <h2 class="heading abs" style="left:112px;top:60px;font-size:35px;font-weight:700;letter-spacing:3px">FAQ</h2>
  <div class="abs" style="left:112px;top:111px;width:78px;height:3px;background:#111"></div>
</section>
<div class="faq-item" style="top:2922px"><div class="q"><span>Lorem ipsum dolor sit amet, consectetur adipiscing elit</span><span>+</span></div></div>
<div class="faq-item" style="top:2978px"><div class="q"><span>Sed do eiusmod tempor incididunt ut labore</span><span>+</span></div></div>
<div class="faq-item" style="top:3034px"><div class="q"><span>Et dolore magna aliqua. Ut enim ad minim</span><span>+</span></div></div>
<div class="faq-item" style="top:3090px;height:148px"><div class="q"><span>Veniam quis nostrud exercitation ullamco laboris nisi</span><span>&minus;</span></div>
  <p class="a">Lorem Ipsum is simply dummy text of the printing and typesetting industry. Lorem Ipsum has been the industry's standard dummy.Lorem Ipsum is simply dummy text of the printing and typesetting industry. Lorem Ipsumng and typesetting industry. Lorem Ipsum has been the industry's standard</p></div>
<div class="faq-item" style="top:3250px"><div class="q"><span>Lorem ipsum dolor sit amet, consectetur adipiscing elit</span><span>+</span></div></div>
<div class="faq-ring"></div>
<div class="faq-photo" role="img" aria-label="Honeycomb, white flowers and a spoon of honey on a bamboo mat"></div>
<div class="jar" role="img" aria-label="Black and pink manuka honey jar" style="left:663px;top:3160px;width:176px;height:190px;background:linear-gradient(90deg,#111,#2a2a2a 60%,#111)"></div>

<footer class="footer">
  <h3 class="f-head" style="left:133px">NAVIGATION</h3>
  <ul class="f-links" style="left:135px"><li>Home</li><li>About Us</li><li>Products</li><li>Videos</li><li>Cotnact Us</li></ul>
  <h3 class="f-head" style="left:350px">USEFUL LINKS</h3>
  <ul class="f-links" style="left:352px"><li>FAQ</li><li>Partnership Inquiries</li><li>Terms</li><li>Shipping &amp; Return</li><li>Cart</li></ul>
  <h3 class="f-head" style="left:604px">NEWSLETTER SIGN UP</h3>
  <p class="abs" style="left:606px;top:115px;font-size:13px;line-height:29.8px">Sign up here to stay up to date</p>
  <div class="email">EMAIL ADDRESS</div>
  <div class="subscribe">SUBSCRIBE</div>
  <h3 class="f-head" style="left:932px">GET IN TOUCH</h3>
  <ul class="f-links f-social" style="left:934px;line-height:34px"><li><i></i>Friendbook</li><li><i></i>Chirper</li><li><i></i>Snapgram</li><li><i></i>WorkLink</li></ul>
  <div class="abs" style="left:0;top:342px;width:1200px;height:1px;background:#2a2a2a"></div>
  <p class="copy">Copyright © 2021 Rimu Vale Honey</p>
</footer>

</body>
</html>
```